Create modern and sleek business card for luxury real estate company

We're a "boutique" real estate office looking for a design that gets across a highly modern luxury brand. Blacks and whites are probably the best colors unless we try a silver foil for the logo. I've attached a version of our current logo here. I'd like to swap out the current font on there with Gotham Light Regular.

I'm looking to have one side of the card have the logo with the space for our agents info on the other side.

Target Market(s)

Young professionals in a "luxury" headspace

Industry/Entity Type

Real estate

Contact Information for Business Card

A place for agent name, cell number, website. The slogan "Quietly Elevating Every Move".

Font styles to use
Other font styles liked:
• Gotham Regular

Colors

Designer to choose only greyscale colors for use in the design.

Requirements
Must have
• Matte black as the background color. Clean lines and use of contrast. A specific design aspect that will use silver foil.
Nice to have
• Up in the air on integrating a QR code
Should not have
• Any houses or other real estate related design (ex: a clip art house)

```html
<!DOCTYPE html>
<html lang="en">
<head>
<meta charset="utf-8">
<title>Solace Realty – Business Card</title>
<link rel="stylesheet" href="https://fonts.googleapis.com/css2?family=Montserrat:wght@300;400;600;700&family=Arimo:wght@400&display=swap">
<style>
  :root {
    --stage: #1c1c1d;
    --matte-black: #262627;
    --matte-black-deep: #1a1a1b;
    --silver: #e9e9ea;
    --paper: #ffffff;
    --ink: #2b2b2c;
    --ink-soft: #8d8d8f;
    --rule: #b5b5b7;
    --accent-grey: #9a9a9c;
  }
  * { box-sizing: border-box; margin: 0; padding: 0; }
  html, body { width: 1200px; height: 900px; overflow: hidden; }
  body {
    background: var(--stage);
    font-family: "Montserrat", sans-serif;
    position: relative;
  }
  .card {
    position: absolute;
    left: 250px;
    width: 700px;
    height: 400px;
    overflow: hidden;
    box-shadow: 0 10px 30px rgba(0,0,0,0.5);
  }
  /* Front: matte black with brand name */
  .card-front { top: 40px; }
  .front-texture {
    position: absolute; inset: 0;
    background: radial-gradient(ellipse at 60% 45%, #333334 0%, var(--matte-black) 55%, var(--matte-black-deep) 100%);
  }
  .brand {
    position: absolute;
    display: flex;
    align-items: center;
    gap: 26px;
  }
  .brand-mark {
    border-radius: 50%;
    flex: none;
  }
  .brand-name {
    font-weight: 300;
    letter-spacing: 0.04em;
    line-height: 1.08;
    text-transform: uppercase;
  }
  .card-front .brand {
    left: 50%; top: 50%;
    transform: translate(-50%, -50%);
  }
  .card-front .brand-mark {
    width: 116px; height: 116px;
    border: 5px solid var(--silver);
  }
  .card-front .brand-name { color: var(--silver); font-size: 58px; }

  /* Back: white with agent details */
  .card-back { top: 470px; background: var(--paper); }
  .card-back .brand {
    left: 50%; top: 36px;
    transform: translateX(-50%);
    gap: 20px;
  }
  .card-back .brand-mark {
    width: 92px; height: 92px;
    border: 4px solid var(--ink);
  }
  .card-back .brand-name { color: var(--ink); font-size: 44px; }

  .divider {
    position: absolute;
    height: 1.5px;
    background: var(--rule);
  }
  .divider-top { left: 80px; right: 80px; top: 160px; }
  .divider-bottom { left: 80px; right: 80px; top: 320px; }

  .agent {
    position: absolute;
    left: 0; right: 0; top: 174px;
    text-align: center;
  }
  .agent-name {
    font-weight: 700;
    font-size: 25px;
    color: var(--ink);
    letter-spacing: 0.02em;
  }
  .agent-role {
    display: flex;
    align-items: center;
    justify-content: center;
    gap: 12px;
    margin-top: 1px;
    font-size: 13px;
    color: var(--ink-soft);
  }
  .agent-role::before,
  .agent-role::after {
    content: "";
    width: 250px;
    height: 1.5px;
    background: var(--rule);
  }

  .contact {
    position: absolute;
    left: 0; right: 0; top: 236px;
    text-align: center;
    font-family: "Arimo", sans-serif;
    color: var(--ink);
  }
  .contact-icons {
    display: flex;
    justify-content: center;
    gap: 14px;
  }
  .contact-icons svg { width: 20px; height: 20px; }
  .contact-line { font-size: 18px; line-height: 1.3; }
  .contact-phone { margin-top: 4px; }
  .contact-web { margin-top: 2px; }

  .footer-band {
    position: absolute;
    left: 0; bottom: 0;
    width: 700px; height: 70px;
  }
  .slogan {
    position: absolute;
    left: 0; right: 0; bottom: 10px;
    text-align: center;
    font-weight: 400;
    font-size: 19px;
    letter-spacing: 0.12em;
    color: var(--silver);
    text-transform: uppercase;
  }
</style>
</head>
<body>

  <section class="card card-front" aria-label="Card front">
    <div class="front-texture" role="img" aria-label="Tone-on-tone embossed brand pattern on matte black"></div>
    <div class="brand">
      <span class="brand-mark"></span>
      <span class="brand-name">Solace<br>Realty</span>
    </div>
  </section>

  <section class="card card-back" aria-label="Card back">
    <div class="brand">
      <span class="brand-mark"></span>
      <span class="brand-name">Solace<br>Realty</span>
    </div>

    <div class="divider divider-top"></div>

    <div class="agent">
      <p class="agent-name">Marcus Veldt</p>
      <p class="agent-role">Agent</p>
    </div>

    <div class="contact">
      <div class="contact-icons">
        <svg viewBox="0 0 20 20" aria-label="Phone">
          <circle cx="10" cy="10" r="10" fill="var(--ink)"/>
          <rect x="7" y="4.5" width="6" height="11" rx="1.2" fill="none" stroke="#fff" stroke-width="1.4"/>
          <circle cx="10" cy="13.3" r="0.8" fill="#fff"/>
        </svg>
        <svg viewBox="0 0 20 20" aria-label="Website">
          <circle cx="10" cy="10" r="10" fill="var(--ink)"/>
          <circle cx="10" cy="10" r="5.2" fill="none" stroke="#fff" stroke-width="1.3"/>
          <ellipse cx="10" cy="10" rx="2.2" ry="5.2" fill="none" stroke="#fff" stroke-width="1.1"/>
          <line x1="4.8" y1="10" x2="15.2" y2="10" stroke="#fff" stroke-width="1.1"/>
        </svg>
      </div>
      <p class="contact-line contact-phone">555 014 2290</p>
      <p class="contact-line contact-web">www.solacerealtyhomes.com</p>
    </div>

    <div class="divider divider-bottom"></div>

    <svg class="footer-band" viewBox="0 0 700 70" aria-hidden="true">
      <rect x="0" y="30" width="108" height="6" fill="var(--accent-grey)"/>
      <rect x="592" y="30" width="108" height="6" fill="var(--accent-grey)"/>
      <polygon points="130,20 570,20 588,40 700,40 700,70 0,70 0,40 112,40" fill="var(--matte-black)"/>
    </svg>
    <p class="slogan">Quietly Elevating Every Move</p>
  </section>

</body>
</html>
```